Brightfen Business Card Redesign & Logo Update

We need to update our business cards to something more modern and fresh. Brightfen can provide the current color schemes and old design examples, but welcome creativity in helping us with this redesign. PLEASE NOTE that we no longer utilize the "tree" and/or "leaf" imagery in our branding. If able would apprecaite an update on the quality of our "words only" logo in Ai. / PNG formats too.

Target Market(s)

Investors, landowners, corporate partners, contractors

Industry/Entity Type

Environmental Restoration & Conservation

Contact Information for Business Card

Logo, persons name, title, mailing address, phone and email, website url

Font styles to use
Other font styles liked:
• Merriweather

Requirements
Nice to have
• Logo, persons name, title, mailing address, phone and email, website url, but open to ideams
Should not have
• No all back backgrounds

```html
<!DOCTYPE html>
<html lang="en">
<head>
<meta charset="utf-8">
<title>Brightfen Business Card</title>
<link rel="stylesheet" href="https://fonts.googleapis.com/css2?family=Merriweather:wght@400;700;900&family=Oswald:wght@500&display=swap">
<style>
  :root {
    --green: #1a7a3c;
    --orange: #ec7a1c;
    --ink: #1c1c1c;
    --paper: #ffffff;
    --backdrop: #d9dadb;
  }
  * { margin: 0; padding: 0; box-sizing: border-box; }
  html, body { width: 1200px; height: 1059px; overflow: hidden; }
  body {
    background: var(--backdrop);
    font-family: "Merriweather", Georgia, serif;
    color: var(--ink);
    position: relative;
  }
  .card {
    position: absolute;
    left: 190px;
    width: 820px;
    height: 469px;
    background: var(--paper);
    box-shadow: 0 6px 18px rgba(0,0,0,0.18);
    overflow: hidden;
  }
  .card--back { top: 40px; }
  .card--front { top: 550px; }

  .wordmark { display: flex; flex-direction: column; align-items: flex-start; }
  .wordmark__name {
    font-family: "Merriweather", Georgia, serif;
    font-weight: 900;
    color: var(--green);
    letter-spacing: 2px;
    line-height: 1;
  }
  .wordmark__tagline {
    font-family: "Oswald", "Arial Narrow", sans-serif;
    font-weight: 500;
    text-transform: uppercase;
    color: var(--ink);
    letter-spacing: 1px;
    line-height: 1;
  }
  .card--back .wordmark {
    position: absolute; left: 50%; top: 50%;
    transform: translate(-50%, -50%);
  }
  .card--back .wordmark__name { font-size: 74px; }
  .card--back .wordmark__tagline { font-size: 25px; margin-top: 8px; }

  .card--front .wordmark { position: absolute; right: 50px; top: 58px; }
  .card--front .wordmark__name { font-size: 56px; }
  .card--front .wordmark__tagline { font-size: 19px; margin-top: 6px; }

  .rule {
    position: absolute; left: 330px; right: 40px; top: 224px;
    height: 2px; background: var(--orange);
  }
  .person { position: absolute; left: 56px; top: 200px; }
  .person__name { font-size: 30px; font-weight: 900; text-transform: uppercase; }
  .person__first { color: var(--orange); }
  .person__last { color: var(--green); }
  .person__title { font-size: 20px; margin-top: 4px; }

  .contact { position: absolute; left: 56px; top: 284px; list-style: none; }
  .contact__item {
    display: flex; align-items: center; gap: 10px;
    font-size: 21px; line-height: 34px;
  }
  .contact__icon { width: 18px; height: 18px; flex: none; }

  .address {
    position: absolute; right: 40px; top: 258px;
    text-align: right; font-size: 20px; line-height: 32px;
  }
  .bands { position: absolute; left: 0; bottom: 0; width: 820px; height: 120px; }
</style>
</head>
<body>

<section class="card card--back">
  <div class="wordmark">
    <span class="wordmark__name">BRIGHTFEN</span>
    <span class="wordmark__tagline">Environmental Credit Company</span>
  </div>
</section>

<section class="card card--front">
  <div class="wordmark">
    <span class="wordmark__name">BRIGHTFEN</span>
    <span class="wordmark__tagline">Environmental Credit Company</span>
  </div>

  <div class="rule"></div>

  <div class="person">
    <div class="person__name"><span class="person__first">Marcus</span> <span class="person__last">Hale</span></div>
    <div class="person__title">Founder</div>
  </div>

  <ul class="contact">
    <li class="contact__item">
      <svg class="contact__icon" viewBox="0 0 18 18" aria-hidden="true">
        <path d="M4 2h3l1.5 4-2 1.3a9 9 0 0 0 4.2 4.2L12 9.5l4 1.5v3a2 2 0 0 1-2 2A13 13 0 0 1 2 4a2 2 0 0 1 2-2z" fill="var(--orange)"/>
      </svg>
      (555) 214-3080
    </li>
    <li class="contact__item">
      <svg class="contact__icon" viewBox="0 0 18 18" aria-hidden="true">
        <rect x="1" y="3" width="16" height="12" rx="1" fill="var(--orange)"/>
        <path d="M1.5 4 9 10l7.5-6" stroke="#fff" stroke-width="1.4" fill="none"/>
      </svg>
      info@brightfenmail.com
    </li>
    <li class="contact__item">
      <svg class="contact__icon" viewBox="0 0 18 18" aria-hidden="true">
        <circle cx="9" cy="9" r="8" fill="var(--orange)"/>
        <path d="M1 9h16M9 1c-3 3-3 13 0 16M9 1c3 3 3 13 0 16" stroke="#fff" stroke-width="1.2" fill="none"/>
      </svg>
      www.brightfen.com
    </li>
  </ul>

  <div class="address">
    418 Marsh Lane<br>
    Suite 12, PO 2718, OR
  </div>

  <svg class="bands" viewBox="0 0 820 120" aria-hidden="true">
    <polygon points="0,64 440,64 520,14 820,14 820,22 525,22 455,72 0,72" fill="var(--green)"/>
    <polygon points="470,120 545,34 820,34 820,62 580,62 530,120" fill="var(--orange)"/>
    <polygon points="0,80 450,80 415,120 0,120" fill="var(--green)"/>
  </svg>
</section>

</body>
</html>
```